Business Card Design

Electronic Security Installation Specialists

Check out our website at www.tallbrookllc.com to see what we do.

Industry/Entity Type

Business

Contact Information for Business Card

Tall Brook
Marjorie Hadley
281 Orchard Rise
Mapleton, WV 25871

Colors
3176b5
0455a3
ffffff

```html
<!DOCTYPE html>
<html lang="en">
<head>
<meta charset="utf-8">
<title>Tall Brook – Business Card</title>
<link href="https://fonts.googleapis.com/css2?family=Didact+Gothic&display=swap" rel="stylesheet">
<style>
  :root {
    --brand-blue: #0455a3;
    --brand-blue-light: #3176b5;
    --brand-navy: #1f3a7a;
    --swoosh-grey: #8a8d91;
    --swoosh-grey-light: #c9cbce;
    --card-white: #ffffff;
    --text-dark: #3a3b3d;
    --page-bg: #e9eaec;
  }
  * { margin: 0; padding: 0; box-sizing: border-box; }
  html, body {
    width: 1200px; height: 900px; overflow: hidden;
    background: var(--page-bg);
    font-family: "Didact Gothic", "Century Gothic", sans-serif;
  }
  .business-card {
    position: absolute; left: 100px; top: 164px;
    width: 1000px; height: 571px;
    background: var(--card-white);
    border-radius: 44px;
    overflow: hidden;
    box-shadow: 0 12px 30px rgba(0,0,0,0.15);
  }
  .card-swoosh { position: absolute; inset: 0; }
  .brand-lockup {
    position: absolute; top: 92px; left: 0; width: 1000px;
    display: flex; justify-content: center; align-items: center; gap: 22px;
  }
  .brand-dot {
    width: 84px; height: 84px; border-radius: 50%;
    background: var(--brand-blue);
  }
  .brand-name {
    font-size: 54px; color: var(--brand-navy); letter-spacing: 1px;
  }
  .identity {
    position: absolute; top: 262px; right: 560px;
    text-align: right; color: var(--text-dark);
    font-variant: small-caps; letter-spacing: 2px;
  }
  .identity .person-name { font-size: 26px; }
  .identity .person-title { font-size: 21px; margin-bottom: 18px; }
  .identity .address-line { font-size: 21px; line-height: 30px; }
  .divider {
    position: absolute; left: 462px; top: 262px;
    width: 1.5px; height: 150px; background: var(--text-dark);
  }
  .contact-list {
    position: absolute; left: 484px; top: 260px;
    list-style: none; color: var(--text-dark);
    font-size: 21px; letter-spacing: 2px; font-variant: small-caps;
  }
  .contact-list li { display: flex; align-items: center; gap: 10px; height: 29px; }
  .contact-list li.web-group { margin-top: 10px; }
  .contact-icon { width: 18px; height: 18px; flex: none; }
</style>
</head>
<body>
  <div class="business-card">
    <svg class="card-swoosh" viewBox="0 0 1000 571" width="1000" height="571" aria-hidden="true">
      <defs>
        <linearGradient id="blueBand" x1="0" y1="0" x2="1" y2="0">
          <stop offset="0" stop-color="#0a3f86"/>
          <stop offset="0.5" stop-color="#3176b5"/>
          <stop offset="1" stop-color="#0455a3"/>
        </linearGradient>
        <linearGradient id="greyBand" x1="0" y1="0" x2="1" y2="0">
          <stop offset="0" stop-color="#7d8085"/>
          <stop offset="1" stop-color="#d4d6d9"/>
        </linearGradient>
      </defs>
      <path d="M0 360 C 180 400, 420 470, 720 505 C 560 470, 300 430, 0 390 Z" fill="url(#greyBand)"/>
      <path d="M0 418 C 220 470, 520 520, 760 530 C 880 535, 960 520, 1000 500 L1000 571 L0 571 Z" fill="url(#blueBand)"/>
    </svg>

    <div class="brand-lockup">
      <span class="brand-dot"></span>
      <span class="brand-name">Tall Brook</span>
    </div>

    <div class="identity">
      <p class="person-name">Marjorie Hadley</p>
      <p class="person-title">Owner / C.E.O</p>
      <p class="address-line">281 Orchard Rise,</p>
      <p class="address-line">Mapleton, WV 25871</p>
    </div>

    <div class="divider"></div>

    <ul class="contact-list">
      <li><svg class="contact-icon" viewBox="0 0 18 18"><circle cx="9" cy="9" r="9" fill="#3a3b3d"/><path d="M6 4.5 L8 6.5 L7 8 Q8 10 10 11 L11.5 10 L13.5 12 L12 13.5 Q8 13.5 4.5 6 Z" fill="#fff"/></svg>304-555-0142</li>
      <li><svg class="contact-icon" viewBox="0 0 18 18"><circle cx="9" cy="9" r="9" fill="#3a3b3d"/><rect x="6.5" y="4" width="5" height="10" rx="1" fill="#fff"/></svg>304-555-0187</li>
      <li><svg class="contact-icon" viewBox="0 0 18 18"><circle cx="9" cy="9" r="9" fill="#3a3b3d"/><rect x="5" y="7" width="8" height="6" fill="#fff"/><rect x="6.5" y="4" width="5" height="3" fill="#fff"/></svg>304-555-0163</li>
      <li class="web-group"><svg class="contact-icon" viewBox="0 0 18 18"><circle cx="9" cy="9" r="9" fill="#3a3b3d"/><rect x="4.5" y="6" width="9" height="6.5" fill="#fff"/><path d="M4.5 6 L9 9.5 L13.5 6" stroke="#3a3b3d" fill="none"/></svg>info@tallbrookllc.com</li>
      <li><svg class="contact-icon" viewBox="0 0 18 18"><circle cx="9" cy="9" r="9" fill="#3a3b3d"/><circle cx="9" cy="9" r="4.5" fill="none" stroke="#fff" stroke-width="1.2"/><path d="M4.5 9 H13.5 M9 4.5 V13.5" stroke="#fff" stroke-width="1"/></svg>www.tallbrookllc.com</li>
    </ul>
  </div>
</body>
</html>
```